Business Card Design Project - del varosi group

dear Sirs

we need business card design for our group ( DEL Varosi Group ) , i have got the Logo design of our group from pixel harbor in previous , so all need details relating to our group i think available with you, as well as the the chosen logo design

we hope to provide us with business card logo that to be appropaite and satisfactory to us .

thanks

note : logo design of our group is attached .
Updates

Reason: please extend the deadline of my project for additional 15 days because i didn't received appropriate design for our gruop yet . kindly beaware that i have received 77 design till now , supossed to send me 200-250 design at least . thanks

Target Market(s)

contents

name : Kerem EL Nadiri

position : Operation Manager

Industry/Entity Type

Business

Requirements
Must have

• person name

group logo
Nice to have
• logo color matching with back background

```html
<!DOCTYPE html>
<html lang="en">
<head>
<meta charset="utf-8">
<title>DEL Varosi Group – Business Card</title>
<link rel="stylesheet" href="https://fonts.googleapis.com/css2?family=Didact+Gothic&display=swap">
<style>
  :root {
    --page-bg: #e9ebee;
    --card-blue: #4a8fd6;
    --card-blue-light: #a9cdf2;
    --card-blue-deep: #3f82cc;
    --stripe-dark: #2b2b2b;
    --stripe-dark-edge: #555;
    --card-grey: #4a4a4a;
    --card-grey-dark: #343434;
    --stripe-blue: #5d9ce0;
    --stripe-blue-light: #a8c9ef;
    --text-light: #ffffff;
    --text-dark: #1c1c1c;
    --mark-grey: #2a2a2a;
  }
  * { box-sizing: border-box; margin: 0; padding: 0; }
  html, body { width: 1067px; height: 1200px; overflow: hidden; }
  body {
    background: var(--page-bg);
    font-family: "Didact Gothic", "Century Gothic", sans-serif;
    position: relative;
  }
  .card {
    position: absolute;
    width: 400px;
    height: 530px;
    overflow: hidden;
    box-shadow: 0 10px 28px rgba(0,0,0,.25);
  }
  .card-front { left: 110px; top: 50px; }
  .card-back { left: 557px; top: 620px; }

  .card-texture { position: absolute; inset: 0; }
  .card-front .card-texture {
    background: radial-gradient(circle at 55% 42%, var(--card-blue-light) 0%, var(--card-blue) 38%, var(--card-blue-deep) 100%);
  }
  .card-back .card-texture {
    background: radial-gradient(circle at 55% 42%, #5a5a5a 0%, var(--card-grey) 40%, var(--card-grey-dark) 100%);
  }

  .card-stripe { position: absolute; top: 0; bottom: 0; left: 0; width: 26px; }
  .card-front .card-stripe { background: linear-gradient(90deg, var(--stripe-dark), var(--stripe-dark-edge)); }
  .card-back .card-stripe { background: linear-gradient(180deg, var(--stripe-blue) 0%, var(--stripe-blue-light) 55%, var(--stripe-blue) 100%); }

  .person { position: absolute; left: 95px; top: 150px; color: var(--text-light); }
  .person-name { font-size: 34px; font-weight: 400; letter-spacing: -0.5px; line-height: 1; }
  .person-role { font-size: 14px; color: var(--text-dark); margin-top: 6px; }

  .contact {
    position: absolute; left: 60px; top: 330px;
    color: var(--text-dark); font-size: 16px; line-height: 24px;
  }
  .contact-company { color: var(--text-light); font-size: 18px; margin-bottom: 4px; }

  .brand-mark {
    position: absolute;
    left: 200px; top: 265px;
    transform: translate(-50%, -50%) rotate(-90deg);
    white-space: nowrap;
    font-size: 44px;
    line-height: 1;
    color: var(--mark-grey);
    letter-spacing: 1px;
  }
</style>
</head>
<body>
  <section class="card card-front" aria-label="Business card front">
    <div class="card-texture" role="img" aria-label="Blue card surface with subtle repeating wave pattern"></div>
    <div class="card-stripe"></div>
    <div class="person">
      <h1 class="person-name">Kerem EL Nadiri</h1>
      <p class="person-role">Operation Manager</p>
    </div>
    <div class="contact">
      <p class="contact-company">DEL Varosi Group</p>
      <p>Phone: 0123 456 789</p>
      <p>Fax: 0123 456 789</p>
      <p>info@yourdomain.com</p>
      <p>www.yourdomain.com</p>
      <p>P.O. Box: City name, etc.</p>
    </div>
  </section>

  <section class="card card-back" aria-label="Business card back">
    <div class="card-texture" role="img" aria-label="Charcoal card surface with subtle repeating wave pattern"></div>
    <div class="card-stripe"></div>
    <p class="brand-mark">DEL VAROSI GROUP</p>
  </section>
</body>
</html>
```